Tallowmere Exteriors Door Hanger design, Postcard and presentation folders Design

we are a home improvement company in Portland Oregon, are main service is roofing but we also do gutters, painting and pressure washing. we are a certified roofing contractor for KRV. We have over 20years of experince in the roofing industry we use top quality materials. Our mission is to do quality work and provide the best service.
Updates

This door hangers are going to be share to homeowners where we are currently working at! I will like to have a square maybe 2 inch wide and 1 inch hide (blank) for me to put the address where we are working at. So we want to give a direct message to homeowners who we are and why we are there for. Our services are roofing, gutters, painting, and pressure washing. But 95% of the door hangers should give the message that we are a roofing contractor. We are also certified by KRV which means all of our new roof projects have a 50 year warranty which only 2% of roofing contractor can offer that. We also offer finance, and all quality work. I will like to add photos of our trucks since all of them are wrap which will build them trust.

Target Market(s)

This door hangers should be custom for Homeowners with residential Homes,,, Average customer are between 40 & 65 Years old.

Industry/Entity Type

Roofing

Contact Information for Business Card

Logo, name, phone number, credentials, and services like roofing gutters painting and pressure washing

Font styles to use
Serif
Sans Serif
Decorative

Colors
33b8a4
5c5c5c

Requirements
Must have
• I want tho have a folder design just like this business card sample i uploaded. Teal and charcoal with services ...
Nice to have
• company trucks, job photo, crew photo and credential photos
Should not have
• I dont want it too busy or crowded..

```html
<!DOCTYPE html>
<html lang="en">
<head>
<meta charset="utf-8">
<title>Tallowmere Exteriors – Flyer</title>
<link rel="stylesheet" href="https://fonts.googleapis.com/css2?family=Oswald:wght@500;600&family=Poppins:wght@600;700&display=swap">
<style>
  :root{
    --teal:#136d65;
    --teal-deep:#0c4a45;
    --teal-bright:#33b8a4;
    --charcoal:#5c5c5c;
    --grey:#8b8b8b;
    --badge:#e2e2e2;
    --white:#ffffff;
    --page:#ffffff;
  }
  *{box-sizing:border-box;margin:0;padding:0}
  html,body{width:1200px;height:844px;overflow:hidden;background:var(--page)}
  body{position:relative;font-family:"Poppins",sans-serif}

  .panel{position:absolute;top:28px;width:554px;height:788px;overflow:hidden;box-shadow:3px 4px 8px rgba(0,0,0,.25)}
  .panel--front{left:30px;background:var(--white)}
  .panel--back{left:614px;background:var(--teal)}

  /* front */
  .brand{position:absolute;top:0;left:0;width:100%;height:212px;display:flex;align-items:center;justify-content:center;gap:14px}
  .brand__mark{width:26px;height:26px;background:var(--charcoal)}
  .brand__name{font-family:"Oswald",sans-serif;font-weight:600;font-size:46px;color:var(--teal);letter-spacing:1px}

  .hero{position:absolute;top:212px;left:0;width:100%;height:289px;
    background:linear-gradient(180deg,#1b6a63 0%,#134a47 55%,#0f3a38 100%);
    display:flex;flex-direction:column;align-items:center;justify-content:center;color:var(--white);text-align:center}
  .hero__title{font-family:"Oswald",sans-serif;font-weight:500;font-size:39px;line-height:45px;letter-spacing:.5px;margin-top:12px}
  .dot{color:var(--grey)}
  .hero__tagline{font-weight:600;font-size:15.5px;margin-top:24px}

  .services{position:absolute;top:501px;left:0;width:100%;height:287px;background:var(--teal);color:var(--white)}
  .services__title{font-family:"Oswald",sans-serif;font-weight:500;font-size:40px;text-align:center;margin-top:18px;letter-spacing:.5px}
  .services__list{list-style:none;position:absolute;top:92px;left:64px;display:grid;grid-template-columns:204px 260px;row-gap:28px}
  .services__item{display:flex;align-items:center;gap:14px;font-weight:700;font-size:20.5px;height:30px;white-space:nowrap}
  .services__item svg{width:30px;height:26px;flex:none}

  /* back */
  .photo{position:absolute}
  .photo--roofline{top:0;left:0;width:554px;height:252px;background:linear-gradient(160deg,#1f7a71 0%,#145e57 45%,#0f4c47 100%)}
  .photo--rooftop{top:252px;left:0;width:554px;height:536px;background:linear-gradient(180deg,#8e8e8c 0%,#6f6f6d 35%,#a7b6c1 60%,#c9d3da 100%)}

  .contact__title{position:absolute;top:34px;left:0;width:100%;text-align:center;font-family:"Oswald",sans-serif;font-weight:500;font-size:44px;color:var(--white);letter-spacing:.5px}
  .phone{position:absolute;top:94px;left:146px;width:286px;height:62px;background:var(--white);border-radius:3px;box-shadow:2px 3px 6px rgba(0,0,0,.3)}
  .phone__number{position:absolute;left:16px;top:9px;font-family:"Oswald",sans-serif;font-weight:500;font-size:29px;line-height:40px;color:var(--teal);white-space:nowrap}
  .phone__tab{position:absolute;right:0;top:10px;width:62px;height:42px}
  .contact__line{position:absolute;left:146px;display:flex;align-items:center;gap:14px;color:var(--white);font-weight:600;font-size:12.5px}
  .contact__line svg{width:18px;height:18px;flex:none}
  .contact__line--address{top:170px}
  .contact__line--email{top:201px}

  .shapes{position:absolute;top:0;left:0;width:554px;height:788px}
  .certified{position:absolute;top:250px;right:40px;text-align:right;font-weight:700;font-size:19px;line-height:25px;color:var(--white)}
  .web{position:absolute;top:520px;left:20px;font-weight:600;font-size:14px;color:var(--white)}
  .web__rule{position:absolute;top:552px;left:20px;width:186px;height:1px;background:rgba(255,255,255,.8)}
  .social{position:absolute;top:582px;left:24px;display:flex;gap:30px}
  .social__dot{width:22px;height:22px;border:2px solid var(--white);border-radius:50%}
</style>
</head>
<body>

<section class="panel panel--front">
  <header class="brand">
    <span class="brand__mark"></span>
    <span class="brand__name">Tallowmere Exteriors</span>
  </header>

  <div class="hero" role="img" aria-label="Photo of a two-storey house with a new shingle roof, tinted teal">
    <h1 class="hero__title">PORTLANT’S TOP-RATED<br>ROOFING COMPANY<span class="dot">.</span></h1>
    <p class="hero__tagline">Let Our Experts Help With Your Next Home Project.</p>
  </div>

  <div class="services">
    <h2 class="services__title">OUR SERVICES<span class="dot">.</span></h2>
    <ul class="services__list">
      <li class="services__item"><svg viewBox="0 0 30 26"><polyline points="3,14 11,22 27,4" fill="none" stroke="#fff" stroke-width="5" stroke-linecap="round" stroke-linejoin="round"/></svg>ROOFING</li>
      <li class="services__item"><svg viewBox="0 0 30 26"><polyline points="3,14 11,22 27,4" fill="none" stroke="#fff" stroke-width="5" stroke-linecap="round" stroke-linejoin="round"/></svg>SIDING</li>
      <li class="services__item"><svg viewBox="0 0 30 26"><polyline points="3,14 11,22 27,4" fill="none" stroke="#fff" stroke-width="5" stroke-linecap="round" stroke-linejoin="round"/></svg>GUTTERS</li>
      <li class="services__item"><svg viewBox="0 0 30 26"><polyline points="3,14 11,22 27,4" fill="none" stroke="#fff" stroke-width="5" stroke-linecap="round" stroke-linejoin="round"/></svg>PRESSURE WASHING</li>
      <li class="services__item"><svg viewBox="0 0 30 26"><polyline points="3,14 11,22 27,4" fill="none" stroke="#fff" stroke-width="5" stroke-linecap="round" stroke-linejoin="round"/></svg>PAINTING</li>
      <li class="services__item"><svg viewBox="0 0 30 26"><polyline points="3,14 11,22 27,4" fill="none" stroke="#fff" stroke-width="5" stroke-linecap="round" stroke-linejoin="round"/></svg>ATTIC VENTILATON</li>
    </ul>
  </div>
</section>

<section class="panel panel--back">
  <div class="photo photo--roofline" role="img" aria-label="Close-up of green house gables and siding, tinted teal"></div>
  <div class="photo photo--rooftop" role="img" aria-label="Close-up of grey roof shingles above a roofer in a safety harness pressure washing a metal roof"></div>

  <svg class="shapes" viewBox="0 0 554 788" aria-hidden="true">
    <polygon points="258,226 554,226 554,368 346,368" fill="#8b8b8b"/>
    <rect x="383" y="368" width="171" height="168" fill="#ffffff"/>
    <rect x="418" y="424" width="104" height="44" rx="4" fill="#e2e2e2"/>
    <polygon points="0,488 264,488 156,630 0,630" fill="#136d65"/>
  </svg>

  <h2 class="contact__title">CONTACT<span class="dot">.</span></h2>

  <div class="phone">
    <span class="phone__number">(503)555-0148</span>
    <svg class="phone__tab" viewBox="0 0 62 42" aria-hidden="true">
      <polygon points="14,0 62,0 62,42 14,42 0,21" fill="#136d65"/>
      <path d="M31 12c-2 1-2 4 0 9s5 9 9 10c2 0 3-1 3-2l-3-3-2 1c-2-1-4-4-5-6l1-2-2-4c-.5-1-1-3-1-3z" fill="#fff"/>
    </svg>
  </div>

  <p class="contact__line contact__line--address">
    <svg viewBox="0 0 18 18" aria-hidden="true"><path d="M9 1.5a5 5 0 0 0-5 5c0 4 5 10 5 10s5-6 5-10a5 5 0 0 0-5-5z" fill="none" stroke="#fff" stroke-width="1.6"/><circle cx="9" cy="6.5" r="1.8" fill="none" stroke="#fff" stroke-width="1.5"/></svg>
    Portland, OR 97209, United States
  </p>
  <p class="contact__line contact__line--email">
    <svg viewBox="0 0 18 18" aria-hidden="true"><rect x="2" y="5" width="14" height="11" fill="none" stroke="#fff" stroke-width="1.6"/><polyline points="2,5 9,11 16,5" fill="none" stroke="#fff" stroke-width="1.6"/></svg>
    info@tallowmereexteriors.com
  </p>

  <p class="certified">OUR COMPANY<br>IS KRV<br>CERTIFIED.</p>

  <p class="web">tallowmereexteriors.com</p>
  <span class="web__rule"></span>
  <div class="social" aria-hidden="true">
    <span class="social__dot"></span>
    <span class="social__dot"></span>
    <span class="social__dot"></span>
  </div>
</section>

</body>
</html>
```